Detail Shop Business card design

i need a business card design for my new detailing company called 'Brisk's Polish Works'. i want an all black and white design . simple, direct and to the point. i want the designer to choose a fitting font to match the logothe front should have logo, address, phone and email and the back side should have a slogan and text indicating that we offer services on anything including cars, trucks, motorcycles and RVs. slogan will read "we take pride in your ride"
maybe also very small on the back side the IG icon with Brisks_Polish_Works

phone 208.417.6352
address 3847 E Larkin Ave
Spokane WA 99214
email: BrisksPolish@mailvexo.com

Target Market(s)

all ages , auto enthusiasts

Industry/Entity Type

Automotive

Contact Information for Business Card

the front should have logo, address, phone and email and the back side should have a slogan and text indicating that we offer services on anything including cars, trucks, motorcycles and RVs. slogan will read "we take pride in your ride"

phone 208.417.6352
address 3847 E Larkin Ave
Spokane WA 99214

Colors
000000
ffffff

Requirements
Must have
• bold font and very simple design with good spacing
Nice to have
• anything creative from the designer indicating we service any types of vehicles
Should not have
• any colors ,

```html
<!DOCTYPE html>
<html lang="en">
<head>
<meta charset="utf-8">
<title>Brisk's Polish Works — Business Card</title>
<link rel="stylesheet" href="https://fonts.googleapis.com/css2?family=Open+Sans:wght@400;600;700;800&display=swap">
<style>
  :root {
    --page: #d9d9d9;
    --card: #121212;
    --ink: #ffffff;
    --ink-soft: #d6d6d6;
    --ink-muted: #a8a8a8;
    --rule: #bdbdbd;
    --art-light: #e4e4e4;
    --art-dark: #8a8a8a;
  }
  * { box-sizing: border-box; margin: 0; padding: 0; }
  html, body {
    width: 1200px; height: 864px; overflow: hidden;
    background: var(--page);
    font-family: "Open Sans", Arial, sans-serif;
  }
  .sheet {
    width: 1200px; height: 864px;
    display: flex; align-items: center; justify-content: center; gap: 40px;
  }
  .card {
    width: 540px; height: 309px;
    background: var(--card);
    color: var(--ink);
    position: relative;
    box-shadow: 0 6px 18px rgba(0,0,0,.25);
  }

  /* Back side */
  .card--back {
    display: flex; flex-direction: column; align-items: center; justify-content: center;
    text-align: center;
  }
  .brand {
    display: flex; align-items: center; gap: 12px;
    font-weight: 800; font-size: 30px; letter-spacing: 1px; text-transform: uppercase;
    color: var(--ink-soft);
  }
  .brand__dot {
    width: 16px; height: 16px; border-radius: 50%; background: var(--ink-soft);
  }
  .slogan {
    margin-top: 34px;
    font-weight: 700; font-size: 17px; letter-spacing: .5px; text-transform: uppercase;
    color: var(--ink-soft);
  }
  .rule {
    width: 370px; height: 1px; background: var(--rule); margin: 8px 0;
  }
  .services {
    font-size: 12px; font-weight: 600; color: var(--ink-muted);
  }

  /* Front side */
  .card--front { display: flex; align-items: center; }
  .vehicle-art {
    width: 200px; height: 110px; margin-left: 34px;
    border-radius: 40px 60px 20px 20px;
    background: linear-gradient(160deg, var(--art-light), var(--art-dark));
  }
  .divider {
    width: 1px; height: 150px; margin: 0 26px 0 34px;
    background: linear-gradient(to bottom, transparent, var(--rule), transparent);
  }
  .contact { font-size: 13px; line-height: 1.45; color: var(--ink-soft); }
  .contact__name { font-weight: 700; font-size: 17px; color: var(--ink); letter-spacing: .5px; line-height: 1.1; }
  .contact__role { font-size: 12px; letter-spacing: .5px; margin-bottom: 8px; }
  .contact__address { margin-bottom: 4px; }
  .contact__row { display: flex; align-items: center; gap: 8px; }
  .contact__row svg { width: 11px; height: 11px; flex: none; fill: var(--ink); }
</style>
</head>
<body>
<main class="sheet">

  <section class="card card--back" aria-label="Back of card">
    <div class="brand"><span class="brand__dot"></span>Brisk's Polish Works</div>
    <p class="slogan">We take pride in your ride</p>
    <div class="rule"></div>
    <p class="services">we offer services on anything including cars, trucks, motorcycles &amp; RVs</p>
    <div class="rule"></div>
  </section>

  <section class="card card--front" aria-label="Front of card">
    <div class="vehicle-art" role="img" aria-label="White illustration of a classic hot rod car in side view"></div>
    <div class="divider"></div>
    <div class="contact">
      <p class="contact__name">MARK HOLLEN</p>
      <p class="contact__role">PRESIDENT</p>
      <p class="contact__address">3847 E Larkin Ave<br>Spokane WA 99214</p>
      <p class="contact__row">
        <svg viewBox="0 0 12 12" aria-hidden="true"><path d="M1 4c0-2 1.5-3 5-3s5 1 5 3v1H8V4H4v1H1z M3 6h6l1 5H2z"/></svg>
        208.417.6352
      </p>
      <p class="contact__row">
        <svg viewBox="0 0 12 12" aria-hidden="true"><path d="M3 0h6v12H3z M4 1.5v8h4v-8z"/></svg>
        836 512 7740
      </p>
      <p class="contact__row">
        <svg viewBox="0 0 12 12" aria-hidden="true"><path d="M0 2h12v8H0z M1 3l5 4 5-4v-.2H1z" fill-rule="evenodd"/></svg>
        BrisksPolish@mailvexo.com
      </p>
      <p class="contact__row">
        <svg viewBox="0 0 12 12" aria-hidden="true"><circle cx="6" cy="6" r="5.5"/></svg>
        www.briskspolish.com
      </p>
    </div>
  </section>

</main>
</body>
</html>
```